Website for legal expungement services with button to qualify/disqualify potential clients

Brightpath Record Renewal, LLC is a law firm focusing in legal expungement servcies (allowing people to erase criminal court records, police records, proseution files, etc). I want a more modern look which exudes confidence in the services. I am looking for a clean website that looks very polished. I want to keep the pages to a minimum, as I want the page not so much to answer questions, but to direct traffic to contact the law office. I would like the main focus point to be an button which would take a client through a series of questions to see if they would qualify for the services; this serves two purposes 1) to collect contact info for future marketing via email and 2) eliminate individuals who we are currently unable to help. A current theme that I have played around with are "Change so much, you'll need to reintroduce yourself" alongside a picture of a guys hand outstretched.
On the landing page, I would like a very brief and to the point explanation of what the service would be (i.e. "Leave your past in the past; expunge all your criminal records" ), followed by a list of benefits that it provides. (NB: included is a file "law post card-02" that includes the main benefits to expungement). Also included are two logo files for a more updated logo I currently use ("BRR Logo" and BRR Logo2") (NB: I'm open to revisions on this as well). Lastly, I've had two very minor 'ads' that I did ("postcard back" and "KVT Ad") that I like the idea of.

Target Market(s)

Middle/upper-middle class, mostly male, people with a criminal record or criminal accusation

Industry/Entity Type

Legal Services

Coding

Coded - Design and coding required

Requirements
Must have
• Button that attracts attention up front (possibly stand out coloring) to click to open up a series of questions to qualify/eliminate prospects, and simultaneously gather their info. Also, must be mobile friendly.

```html
<!DOCTYPE html>
<html lang="en">
<head>
<meta charset="utf-8">
<title>Brightpath Record Renewal</title>
<link rel="stylesheet" href="https://fonts.googleapis.com/css2?family=Cinzel:wght@400;600;700&family=Open+Sans:wght@300;400;600&family=Montserrat:wght@600;700&display=swap">
<style>
:root{
  --navy:#0a3a73;
  --ink:#1f1f1f;
  --text:#333;
  --muted:#8a8a8a;
  --footer:#262626;
  --white:#fff;
  --line:#dedede;
}
*{box-sizing:border-box;margin:0;padding:0}
html,body{width:1200px;height:3565px;overflow:hidden;background:var(--white)}
body{position:relative;font-family:"Open Sans",Arial,sans-serif;color:var(--text)}
.abs{position:absolute}
.serif{font-family:"Cinzel",Georgia,serif}
.btn{position:absolute;display:flex;align-items:center;justify-content:center;font-family:"Montserrat",Arial,sans-serif;font-weight:700;font-size:16px;letter-spacing:.3px;text-decoration:none}
.btn--solid{background:var(--navy);color:var(--white)}
.btn--outline{border:3px solid var(--navy);color:var(--navy);background:transparent;font-family:"Cinzel",Georgia,serif;font-size:17px}

/* header */
.brand-mark{left:111px;top:40px;height:42px;display:flex;align-items:center;gap:12px;font-family:"Cinzel",Georgia,serif;font-weight:600;font-size:26px;color:var(--navy)}
.brand-mark i{display:block;width:18px;height:18px;background:var(--navy)}
.brand-divider{left:259px;top:15px;width:2px;height:87px;background:var(--navy)}
.brand-name{left:295px;top:38px;color:var(--navy);font-size:17px;line-height:22px;font-weight:600}
.main-nav{left:536px;top:49px;display:flex;gap:36px;font-size:15px;color:var(--ink)}
.login{left:977px;top:33px;width:111px;height:51px;font-family:"Cinzel",serif;font-size:17px}

/* hero */
.hero-title{left:113px;top:258px;color:var(--navy);font-size:48px;line-height:69px;font-weight:700;letter-spacing:1px}
.hero-cta{left:111px;top:497px;width:249px;height:51px}

/* cases */
.cases-frame{left:123px;top:914px;width:382px;height:378px;border:3px solid var(--navy);border-top-right-radius:70px}
.cases-photo{left:113px;top:922px;width:384px;height:375px;border-top-right-radius:70px;background:linear-gradient(120deg,#121212 0%,#2a2f3a 45%,#8b9bb2 70%,#1a1a1a 100%)}
.section-title{color:var(--ink);font-size:30px;font-weight:600}
.section-title em{font-style:normal;color:var(--navy)}
.cases-title{left:597px;top:935px}
.check-list{left:597px;top:1015px;list-style:none;width:460px;font-size:19px;line-height:30px;color:var(--text)}
.check-list li{position:relative;padding-left:42px;margin-bottom:18px}
.check-list svg{position:absolute;left:0;top:8px}
.cases-cta{left:598px;top:1217px;width:146px;height:51px;font-family:"Cinzel",serif;font-size:17px}

/* benefits */
.benefits-band{left:0;top:1383px;width:1200px;height:857px;background:linear-gradient(100deg,#ededf0 0%,#e6e6ea 40%,#dcdde2 70%,#ececef 100%)}
.benefits-title{left:0;top:1462px;width:1200px;text-align:center}
.benefit{position:absolute;width:300px;text-align:center;font-size:17px;line-height:30px;color:var(--ink)}
.benefit svg{display:block;margin:0 auto 18px}
.benefit--active{background:var(--white);box-shadow:0 4px 14px rgba(0,0,0,.08)}
.view-all{left:522px;top:2101px;width:155px;height:50px}

/* services */
.services-title{left:0;top:2320px;width:1200px;text-align:center}
.service-card{position:absolute;top:2402px;width:481px;height:539px;border:1px solid var(--line);background:var(--white)}
.service-photo{height:218px}
.service-card h3{font-family:"Cinzel",serif;font-weight:600;font-size:21px;color:var(--ink);margin:24px 0 0 28px}
.service-card p{font-size:13px;line-height:23px;color:var(--muted);margin:26px 28px 0 28px;font-weight:300}
.service-card .btn{left:29px;bottom:37px;width:147px;height:51px}

/* footer */
.foot-mark{left:111px;top:3248px;height:62px;display:flex;align-items:center;gap:14px;font-family:"Cinzel",Georgia,serif;font-weight:600;font-size:36px;color:var(--white)}
.foot-mark i{display:block;width:24px;height:24px;background:var(--white)}
.foot-divider{left:324px;top:3218px;width:2px;height:117px;background:#9a9a9a}
.foot-brand{left:376px;top:3250px;color:var(--white);font-size:22px;line-height:30px;font-weight:600}
.copyright{left:111px;top:3374px;width:220px;color:var(--white);font-size:13px;line-height:24px}
.socials{left:111px;top:3444px;display:flex;gap:22px}
.socials span{width:20px;height:20px;border-radius:50%;background:var(--white)}
.address-title{left:379px;top:3380px;color:var(--white);font-size:19px;font-weight:600}
.contact-lines{left:379px;top:3413px;color:#e6e6e6;font-size:15px;line-height:30px}
.contact-lines div{position:relative;padding-left:31px}
.contact-lines svg{position:absolute;left:0;top:9px}
.form-title{left:697px;top:3215px;color:var(--white);font-size:26px;font-weight:600}
.field{position:absolute;left:697px;width:391px;background:var(--white);border-radius:2px;color:#555;font-size:13px;padding:14px 14px}
.submit{left:697px;top:3483px;width:391px;height:42px;font-family:"Cinzel",serif;font-size:18px;font-weight:600}
</style>
</head>
<body>

<header>
  <div class="abs brand-mark"><i></i>BRR</div>
  <div class="abs brand-divider"></div>
  <div class="abs brand-name serif">BRIGHTPATH RECORD<br>RENEWAL</div>
  <nav class="abs main-nav"><span>HOME</span><span>ABOUT US</span><span>SERVICES</span><span>CONTACT US</span></nav>
  <a class="btn btn--solid login">LOG IN</a>
</header>

<section class="hero">
  <svg class="abs" style="left:0;top:120px" width="1200" height="712" viewBox="0 120 1200 712">
    <defs>
      <linearGradient id="heroFill" x1="0" y1="0" x2="1" y2="1">
        <stop offset="0" stop-color="#efe6d6"/>
        <stop offset=".5" stop-color="#f1dcc0"/>
        <stop offset=".8" stop-color="#dea277"/>
        <stop offset="1" stop-color="#c88658"/>
      </linearGradient>
    </defs>
    <polygon role="img" aria-label="Two hands reaching toward each other in warm light" points="0,120 1200,120 1200,640 600,808 0,640" fill="url(#heroFill)"/>
    <polygon points="0,640 600,808 1200,640 1200,656 600,830 0,656" fill="#0a3a73"/>
  </svg>
  <h1 class="abs hero-title serif">CHANGE SO MUCH,<br>YOU'LL NEED TO<br>REINTRODUCE YOURSELF</h1>
  <a class="btn btn--outline hero-cta">BOOK AN APPOINTMENT</a>
</section>

<section class="cases">
  <div class="abs cases-frame"></div>
  <div class="abs cases-photo" role="img" aria-label="Client in a consultation meeting across a desk"></div>
  <h2 class="abs section-title serif cases-title">What types of <em>cases qualify</em></h2>
  <ul class="abs check-list">
    <li><svg width="18" height="18" viewBox="0 0 18 18"><circle cx="9" cy="9" r="9" fill="#0a3a73"/><path d="M5 9.3l2.6 2.5L13 6.5" stroke="#fff" stroke-width="2" fill="none"/></svg>Criminal accusations that were dismissed</li>
    <li><svg width="18" height="18" viewBox="0 0 18 18"><circle cx="9" cy="9" r="9" fill="#0a3a73"/><path d="M5 9.3l2.6 2.5L13 6.5" stroke="#fff" stroke-width="2" fill="none"/></svg>Criminal cases that went into a diversionary program</li>
    <li><svg width="18" height="18" viewBox="0 0 18 18"><circle cx="9" cy="9" r="9" fill="#0a3a73"/><path d="M5 9.3l2.6 2.5L13 6.5" stroke="#fff" stroke-width="2" fill="none"/></svg>Convictions</li>
  </ul>
  <a class="btn btn--solid cases-cta">LEARN MORE</a>
</section>

<section class="benefits">
  <div class="abs benefits-band" role="img" aria-label="Faded background of a legal consultation"></div>
  <h2 class="abs section-title serif benefits-title">Benefits to <em>Expunging</em></h2>

  <div class="benefit" style="left:113px;top:1570px">
    <svg width="90" height="90" viewBox="0 0 90 90" fill="none" stroke="#0a3a73" stroke-width="3"><path d="M36 10h18l-5 10h-8z"/><circle cx="45" cy="40" r="18"/><path d="M5 62l16-8 16 6h14l-2 6H32M21 54l-8 24 8 2"/><path d="M51 66l24-14c5-2 7 3 3 6L55 76H28"/><text x="45" y="46" font-size="18" fill="#0a3a73" stroke="none" text-anchor="middle" font-family="Arial">$</text></svg>
    More And Better Job<br>Opportunities Leading TO<br>Higher Income
  </div>
  <div class="benefit benefit--active" style="left:449px;top:1547px;height:263px;padding-top:26px">
    <svg width="90" height="90" viewBox="0 0 90 90" fill="none" stroke="#0a3a73" stroke-width="3"><rect x="16" y="8" width="48" height="72" rx="2"/><path d="M24 22h24M24 44h32M24 52h32M24 60h20"/><text x="20" y="36" font-size="14" fill="#0a3a73" stroke="none" font-family="Arial" font-weight="bold">LOAN</text><path d="M74 14l6 6-24 32-8 3 2-8z"/></svg>
    Loan Qualification Amd Better<br>Loan Rates
  </div>
  <a class="btn btn--solid" style="left:526px;top:1787px;width:148px;height:51px">LEARN MORE</a>
  <div class="benefit" style="left:786px;top:1570px">
    <svg width="90" height="90" viewBox="0 0 90 90" fill="none" stroke="#0a3a73" stroke-width="3"><path d="M45 8l28 10v22c0 20-12 32-28 40C29 72 17 60 17 40V18z"/><circle cx="45" cy="36" r="8"/><path d="M31 60c2-10 26-10 28 0"/><circle cx="64" cy="64" r="10"/><path d="M59 64l4 4 6-7"/></svg>
    Protecting Your Privacy
  </div>

  <div class="benefit" style="left:113px;top:1880px">
    <svg width="90" height="90" viewBox="0 0 90 90" fill="none" stroke="#0a3a73" stroke-width="3"><path d="M12 76h66v-10H12zM16 66h60V56H16zM12 56h66V46H12z"/><path d="M22 28l24-10 24 10-24 10z"/><path d="M32 32v8c8 5 20 5 28 0v-8"/><path d="M70 28v12"/></svg>
    Better Education Opportunities
  </div>
  <div class="benefit" style="left:449px;top:1880px">
    <svg width="90" height="90" viewBox="0 0 90 90" fill="none" stroke="#0a3a73" stroke-width="3"><rect x="16" y="10" width="48" height="70" rx="2"/><circle cx="40" cy="32" r="10"/><path d="M26 54h28M26 62h28M26 70h18"/><path d="M74 16l6 6-20 30-8 3 2-8z"/></svg>
    Removing The Stigma Of<br>Having &nbsp;A Criminal Record
  </div>
  <div class="benefit" style="left:786px;top:1880px">
    <svg width="90" height="90" viewBox="0 0 90 90" fill="none" stroke="#0a3a73" stroke-width="3"><path d="M8 44L45 10l37 34"/><path d="M18 36v44h54V36"/><rect x="32" y="46" width="26" height="24"/><path d="M45 46v24M32 58h26M62 18v12"/><path d="M10 80h70"/></svg>
    More Options for Housing
  </div>
  <a class="btn btn--outline view-all">VIEW ALL</a>
</section>

<section class="services">
  <h2 class="abs section-title serif services-title">Our <em>Services</em></h2>
  <article class="service-card" style="left:105px">
    <div class="service-photo" role="img" aria-label="Business team smiling in a bright office meeting" style="background:linear-gradient(110deg,#c9c2b4 0%,#2b3550 35%,#e9e4dc 60%,#4d4a54 85%,#d8cbb5 100%)"></div>
    <h3>Leave your past in the past</h3>
    <p>Sed ut perspiciatis unde omnis iste natus error sit volupt accusantium Sed ut perspiciatis unde omnis iste natus error sit volupta accusantium doloremquloremqueSed ut perspiciatis unde omnis iste natus error sit voluptatem accusantium &nbsp;Duis aute irure dolor in reprehenderitin voluptate velit esse cillum dolore eu fugiat nulla pariatur.</p>
    <a class="btn btn--solid">LEARN MORE</a>
  </article>
  <article class="service-card" style="left:613px">
    <div class="service-photo" role="img" aria-label="Tablet showing a criminal records document" style="background:linear-gradient(120deg,#3c5f93 0%,#6f8fbd 35%,#e4ebf4 60%,#8da6c8 80%,#2f4d7d 100%)"></div>
    <h3>Expunge all your criminal records</h3>
    <p>Sed ut perspiciatis unde omnis iste natus error sit volupt accusantium Sed ut perspiciatis unde omnis iste natus error sit volupta accusantium doloremquloremqueSed ut perspiciatis unde omnis iste natus error sit voluptatem accusantium &nbsp;Duis aute irure dolor in reprehenderitin voluptate velit esse cillum dolore eu fugiat nulla pariatur.</p>
    <a class="btn btn--solid">LEARN MORE</a>
  </article>
</section>

<footer>
  <svg class="abs" style="left:0;top:3020px" width="1200" height="545" viewBox="0 3020 1200 545">
    <polygon points="0,3198 600,3027 1200,3198 1200,3565 0,3565" fill="#0a3a73"/>
    <polygon points="0,3214 600,3046 1200,3214 1200,3565 0,3565" fill="#262626"/>
  </svg>
  <div class="abs foot-mark"><i></i>BRR</div>
  <div class="abs foot-divider"></div>
  <div class="abs foot-brand serif">BRIGHTPATH RECORD<br>RENEWAL</div>
  <p class="abs copyright">Copyright © 2023 Brightpath Record Renewal All rights reserved</p>
  <div class="abs socials"><span></span><span></span><span></span><span></span><span></span></div>

  <h4 class="abs address-title serif">Address</h4>
  <div class="abs contact-lines">
    <div><svg width="18" height="14" viewBox="0 0 18 14"><path d="M1 2l5-2 6 2 5-2v12l-5 2-6-2-5 2z" fill="#3b7bd1"/></svg>Lorem ipsum dolor sit amet,<br>sed do eiusmod tempor incididunt</div>
    <div><svg width="16" height="16" viewBox="0 0 16 16"><path d="M3 1l3 3-2 2c1 3 3 5 6 6l2-2 3 3-2 3C6 15 1 10 0 3z" fill="#3b7bd1"/></svg>555-014-2290</div>
    <div><svg width="16" height="12" viewBox="0 0 16 12"><rect width="16" height="12" rx="1" fill="#3b7bd1"/><path d="M0 1l8 6 8-6" stroke="#262626" stroke-width="1.5" fill="none"/></svg>hello@brightpathrenewal.example</div>
  </div>

  <h4 class="abs form-title serif">Contact Us</h4>
  <div class="field" style="top:3270px;height:45px">Name</div>
  <div class="field" style="top:3323px;height:45px">Email Address</div>
  <div class="field" style="top:3378px;height:90px">Message</div>
  <a class="btn btn--solid submit">SUBMIT NOW</a>
</footer>

</body>
</html>
```